Vantiqo custom business card design

Need a authentic, innovative business card design for a new mobile app business. I am uploading a few screen images from our app for you to view. I would like app design theme to match business card design. I can also send logo images.

```html
<!DOCTYPE html>
<html lang="en">
<head>
<meta charset="UTF-8">
<title>Vantiqo Business Card</title>
<link href="https://fonts.googleapis.com/css2?family=Montserrat:wght@700;800&family=Open+Sans:wght@400&display=swap" rel="stylesheet">
<style>
  :root {
    --page-bg: #e9e7ea;
    --card-light: #f7f6f7;
    --card-dark: #1f1f1f;
    --brand-purple: #6a0aa0;
    --ink-dark: #1c1c1c;
    --ink-light: #ffffff;
  }
  html, body {
    margin: 0;
    padding: 0;
    width: 1200px;
    height: 900px;
    overflow: hidden;
    background: var(--page-bg);
  }
  .canvas {
    width: 1200px;
    height: 900px;
    display: flex;
    align-items: center;
    justify-content: center;
  }
  .business-card {
    width: 900px;
    height: 556px;
    display: flex;
    box-shadow: 0 18px 40px rgba(0,0,0,0.18);
  }
  .brand-side {
    width: 458px;
    background: var(--card-light);
    display: flex;
    align-items: center;
    justify-content: center;
    gap: 18px;
  }
  .brand-dot {
    width: 46px;
    height: 46px;
    border-radius: 50%;
    background: var(--brand-purple);
  }
  .brand-name {
    font-family: 'Montserrat', sans-serif;
    font-weight: 800;
    font-size: 62px;
    color: var(--ink-dark);
    letter-spacing: 0.5px;
  }
  .divider {
    width: 4px;
    background: var(--brand-purple);
  }
  .info-side {
    flex: 1;
    background: var(--card-dark);
    padding: 68px 0 0 41px;
    color: var(--ink-light);
    font-family: 'Open Sans', sans-serif;
    box-sizing: border-box;
  }
  .person-name {
    font-family: 'Montserrat', sans-serif;
    font-weight: 800;
    font-size: 33px;
    color: var(--brand-purple);
    margin: 0;
    line-height: 1.1;
  }
  .person-role {
    font-size: 25px;
    margin: 4px 0 0;
  }
  .contact-list {
    list-style: none;
    margin: 148px 0 0;
    padding: 0;
    font-size: 25px;
    line-height: 32px;
  }
  .contact-list li {
    display: flex;
    align-items: center;
    gap: 6px;
  }
  .contact-icon {
    width: 20px;
    height: 20px;
    fill: var(--brand-purple);
    flex: none;
  }
  .address {
    font-size: 25px;
    line-height: 33px;
    margin: 22px 0 0;
  }
</style>
</head>
<body>
<div class="canvas">
  <div class="business-card">
    <div class="brand-side">
      <span class="brand-dot"></span>
      <span class="brand-name">Vantiqo</span>
    </div>
    <div class="divider"></div>
    <div class="info-side">
      <h1 class="person-name">MARCUS ELLERY</h1>
      <p class="person-role">Managing Director</p>
      <ul class="contact-list">
        <li>
          <svg class="contact-icon" viewBox="0 0 20 20"><path d="M2 7c0-3 3-4 8-4s8 1 8 4v2h-4V7H6v2H2zM5 10h10l2 7H3z"/></svg>
          055-987 321 640
        </li>
        <li>
          <svg class="contact-icon" viewBox="0 0 20 20"><path d="M6 1h8a1 1 0 0 1 1 1v16a1 1 0 0 1-1 1H6a1 1 0 0 1-1-1V2a1 1 0 0 1 1-1zm1 2v12h6V3zm3 13a1 1 0 1 0 0 2 1 1 0 0 0 0-2z"/></svg>
          055-987 321 640
        </li>
        <li>
          <svg class="contact-icon" viewBox="0 0 20 20"><path d="M2 4h16v12H2zm1.5 1.5L10 11l6.5-5.5z"/></svg>
          hello@vantiqo.app
        </li>
        <li>
          <svg class="contact-icon" viewBox="0 0 20 20"><circle cx="10" cy="10" r="8"/><path d="M2 10h16M10 2c3 3 3 13 0 16M10 2c-3 3-3 13 0 16" stroke="#1f1f1f" stroke-width="1.2" fill="none"/></svg>
          www.vantiqo.app
        </li>
      </ul>
      <p class="address">12345, Address Goes Here<br>Country Name, 123456</p>
    </div>
  </div>
</div>
</body>
</html>
```